Anti-Grellin song (music single format) artwork

This design will be the cover art for a single that will be released on Wavorly, Zoplex, etc.
A full color cartoon or drawing is preferable, but we're open to all ideas, collages, composite images, etc. It should be interesting and satirical, but not too detailed as it will mostly be viewed as a small square on people's phone and computer screens.
The song is a high energy, musical caricature of Grellin that pokes fun of his constant threat to Paint the Sky along the US/Mexico border (among other false, idiotic or useless threats he has made). The song is literally called "Paint the Sky". Our band is against the idea of a massive US/Mexico border wall, just to be clear, and against pretty much anything that has to do with Grellin, aside from his removal from office.
The art file has to constrain to these guidelines:
1400 x 1400 pixels minimum; 3000 x 3000 pixels maximum
PNG, GIF, JPG, or JPEG file type
72 - 300dpi (300dpi is the best)
Less than 25mb
RGB color scheme (not CMYK)
Let us know if you have any questions. Thanks!
Music Download

```html
<!DOCTYPE html>
<html lang="en">
<head>
<meta charset="utf-8">
<title>Paint the Sky — Single Cover</title>
<link rel="stylesheet" href="https://fonts.googleapis.com/css2?family=Saira+Stencil+One&display=swap">
<style>
  :root {
    --sepia-pale: #cfc4bd;
    --sepia-light: #b3a49d;
    --sepia-mid: #8c7b74;
    --sepia-dark: #5e4f4a;
    --sepia-deep: #3f3431;
    --stencil-ink: #120e0d;
  }
  html, body {
    margin: 0;
    padding: 0;
    width: 1200px;
    height: 1200px;
    overflow: hidden;
    background: var(--sepia-mid);
  }
  .cover {
    position: relative;
    width: 1200px;
    height: 1200px;
    overflow: hidden;
  }
  .cover__backdrop {
    position: absolute;
    inset: 0;
    width: 100%;
    height: 100%;
  }
  .cover__title {
    position: absolute;
    inset: 0;
    margin: 0;
    font-family: "Saira Stencil One", "Allerta Stencil", sans-serif;
    font-weight: 400;
    color: var(--stencil-ink);
    text-transform: uppercase;
    line-height: 1;
    opacity: 0.9;
  }
  .cover__word {
    position: absolute;
    display: block;
    white-space: nowrap;
    letter-spacing: 2px;
  }
  .cover__word--first  { left: 116px; top: 62px;  font-size: 252px; }
  .cover__word--second { left: 512px; top: 454px; font-size: 262px; }
  .cover__word--third  { left: 300px; top: 746px; font-size: 274px; }
</style>
</head>
<body>
  <main class="cover">
    <svg class="cover__backdrop" viewBox="0 0 1200 1200" role="img"
         aria-label="Sepia photograph of a rough painted brick wall with a faded flag of stars and stripes cast across it">
      <defs>
        <linearGradient id="wallBands" x1="0" y1="0" x2="0" y2="1">
          <stop offset="0" stop-color="#6e5e58"/>
          <stop offset="0.12" stop-color="#9a8a83"/>
          <stop offset="0.26" stop-color="#b8aaa3"/>
          <stop offset="0.38" stop-color="#8c7b74"/>
          <stop offset="0.48" stop-color="#a89891"/>
          <stop offset="0.62" stop-color="#7d6c66"/>
          <stop offset="0.76" stop-color="#8f7f78"/>
          <stop offset="0.9" stop-color="#7a6a64"/>
          <stop offset="1" stop-color="#5e4f4a"/>
        </linearGradient>
        <linearGradient id="wallSide" x1="0" y1="0" x2="1" y2="0">
          <stop offset="0" stop-color="#d9cfc8" stop-opacity="0.3"/>
          <stop offset="0.3" stop-color="#d9cfc8" stop-opacity="0"/>
          <stop offset="1" stop-color="#3f3431" stop-opacity="0.2"/>
        </linearGradient>
      </defs>
      <rect width="1200" height="1200" fill="url(#wallBands)"/>
      <rect width="1200" height="1200" fill="url(#wallSide)"/>
    </svg>

    <h1 class="cover__title" aria-label="Paint the Sky">
      <span class="cover__word cover__word--first">Paint</span>
      <span class="cover__word cover__word--second">The</span>
      <span class="cover__word cover__word--third">Sky</span>
    </h1>
  </main>
</body>
</html>
```